Velvet Riot Rising Line of Sparkling Wine & Spirits

Back info: Nora Beth Quill Owner 555-318-4402 1480 E. Harlow Ave, Bldg. 2, & 3, Ashvale Co. 95871
Sparkling Wines & Memorabilia www.velvetriotrising.com
Ok I have uploaded the winning design. The color that I am after is the Fushia, Raspberry, Red, Matte Satin Matalic Finish. With a 24 Karet Gold color Foil. The Bottle is on the top row and it's the 2nd Bottle in. That is the Color that I want. This is the style of font. Make sure that you put what we're advertising. Good Luck to you all. Warmest regards, Nora
21 & up UniSex
Sparkling Wine and Memorabilia
there listed up above.....

```html
<!DOCTYPE html>
<html lang="en">
<head>
<meta charset="utf-8">
<title>Velvet Riot Rising – Business Card</title>
<link rel="stylesheet" href="https://fonts.googleapis.com/css2?family=Arimo:wght@400;700&display=swap">
<style>
  :root {
    --page: #e4e4e4;
    --card-white: #ffffff;
    --fuchsia: #d3147f;
    --fuchsia-deep: #8f1250;
    --fuchsia-bright: #e31a96;
    --gold: #e8b13a;
    --ink: #4a4a4a;
    --logo-ink: #3a3a3a;
    --tagline: #ffffff;
  }
  * { box-sizing: border-box; margin: 0; padding: 0; }
  html, body { width: 1200px; height: 1200px; overflow: hidden; }
  body {
    background: var(--page);
    font-family: "Arimo", Arial, sans-serif;
    position: relative;
  }
  .card {
    position: absolute;
    left: 256px;
    width: 690px;
    height: 394px;
    overflow: hidden;
  }
  .card--contact { top: 159px; background: var(--card-white); }
  .card--brand {
    top: 653px;
    left: 262px;
    background: radial-gradient(ellipse at 52% 42%, var(--fuchsia-bright) 0%, var(--fuchsia) 40%, var(--fuchsia-deep) 100%);
  }

  .holder { position: absolute; left: 65px; top: 108px; }
  .holder__name {
    color: var(--fuchsia);
    font-weight: 700;
    font-size: 26px;
    letter-spacing: 0.2px;
    line-height: 1;
  }
  .holder__role {
    color: var(--gold);
    font-size: 17px;
    margin-top: 3px;
  }
  .address {
    position: absolute;
    left: 65px;
    top: 182px;
    color: var(--ink);
    font-size: 16px;
    line-height: 21px;
  }
  .contacts {
    position: absolute;
    left: 63px;
    top: 252px;
    list-style: none;
    color: var(--ink);
    font-size: 16px;
    line-height: 21px;
  }
  .contacts li { display: flex; align-items: center; gap: 10px; }
  .contacts svg { width: 14px; height: 14px; flex: none; }

  .bottle {
    position: absolute;
    border-radius: 14px 14px 18px 18px;
    background: linear-gradient(90deg, #b80f69 0%, var(--fuchsia-bright) 45%, #c9117a 70%, #8f0d50 100%);
  }
  .card--contact .bottle { left: 531px; top: 47px; width: 90px; height: 305px; }
  .card--brand .bottle { left: 102px; top: 65px; width: 74px; height: 256px; }

  .brandmark { position: absolute; left: 190px; top: 160px; }
  .brandmark__name {
    color: var(--logo-ink);
    font-weight: 700;
    font-size: 44px;
    line-height: 1;
    letter-spacing: 0.5px;
  }
  .brandmark__rule {
    height: 1px;
    width: 365px;
    margin: 12px 0 10px;
    background: rgba(255,255,255,0.35);
  }
  .brandmark__tagline {
    color: var(--tagline);
    font-size: 17.5px;
    letter-spacing: 2px;
  }
  .brandmark__tagline strong { font-weight: 700; }
</style>
</head>
<body>

  <section class="card card--contact" aria-label="Business card, contact side">
    <div class="holder">
      <h1 class="holder__name">NORA BETH QUILL</h1>
      <p class="holder__role">Owner</p>
    </div>
    <p class="address">E. Harlow Ave<br>Bldg. 2, &amp; 3, Ashvale Co. 95871</p>
    <ul class="contacts">
      <li>
        <svg viewBox="0 0 16 16" aria-hidden="true"><path fill="var(--fuchsia)" d="M3.6 1.2l2.3 2.7-1.3 1.9c.9 2 2.6 3.7 4.6 4.6l1.9-1.3 2.7 2.3-1.2 2.4C7.4 15.6.4 8.6 1.2 2.4z"/></svg>
        555-318-4402 1480
      </li>
      <li>
        <svg viewBox="0 0 16 16" aria-hidden="true"><circle cx="8" cy="8" r="7" fill="var(--fuchsia)"/><path d="M1 8h14M8 1c-3 3-3 11 0 14M8 1c3 3 3 11 0 14" stroke="#fff" stroke-width="1.1" fill="none"/></svg>
        www.velvetriotrising.com
      </li>
      <li>
        <svg viewBox="0 0 16 16" aria-hidden="true"><circle cx="8" cy="8" r="7" fill="var(--fuchsia)"/></svg>
        @velvetriotrising
      </li>
      <li>
        <svg viewBox="0 0 16 16" aria-hidden="true"><rect x="1" y="1" width="14" height="14" rx="3" fill="var(--fuchsia)"/></svg>
        @velvetriotrising
      </li>
    </ul>
    <div class="bottle" role="img" aria-label="Illustration of a fuchsia sparkling wine bottle with gold foil neck and crest label"></div>
  </section>

  <section class="card card--brand" aria-label="Business card, brand side">
    <div class="bottle" role="img" aria-label="Illustration of a fuchsia sparkling wine bottle with gold foil neck and crest label"></div>
    <div class="brandmark">
      <p class="brandmark__name">Velvet Riot Rising</p>
      <div class="brandmark__rule"></div>
      <p class="brandmark__tagline">SPARKLING <strong>WINES &amp; MEMORABILIA</strong></p>
    </div>
  </section>

</body>
</html>
```